Business Card

Just need business logo with phone number on it. 0487 312 654
And the following on the bottom of the card.

"Your local plumbing experts".
and emblems for zelpa card, cheque and cash

```html
<!DOCTYPE html>
<html lang="en">
<head>
<meta charset="UTF-8">
<title>Ridgeline Plumbing – Business Card</title>
<link href="https://fonts.googleapis.com/css2?family=Open+Sans:wght@400;700&display=swap" rel="stylesheet">
<style>
  :root {
    --backdrop: #7a5237;
    --card-dark: #000000;
    --card-light: #ffffff;
    --brand-red: #e3262e;
    --brand-blue: #2a8fd6;
    --ink: #555a5f;
    --ink-strong: #3d4246;
  }
  * { margin: 0; padding: 0; box-sizing: border-box; }
  html, body {
    width: 1200px;
    height: 1000px;
    overflow: hidden;
  }
  body {
    position: relative;
    background: var(--backdrop);
    font-family: "Open Sans", sans-serif;
  }
  .card {
    position: absolute;
    left: 266px;
    width: 666px;
    height: 397px;
    box-shadow: 0 4px 14px rgba(0,0,0,0.35);
  }
  .card--front {
    top: 74px;
    background: var(--card-dark);
    display: flex;
    align-items: center;
    justify-content: center;
  }
  .card--back {
    top: 533px;
    background: var(--card-light);
    text-align: center;
  }
  .brand {
    display: inline-flex;
    align-items: center;
    gap: 14px;
  }
  .brand__dot {
    width: 26px;
    height: 26px;
    border-radius: 50%;
    background: var(--brand-blue);
  }
  .brand__name {
    font-weight: 700;
    font-size: 42px;
    letter-spacing: 1px;
    color: var(--brand-red);
    text-transform: uppercase;
  }
  .card--back .brand {
    margin-top: 92px;
  }
  .contact__name {
    margin-top: 60px;
    font-weight: 700;
    font-size: 22px;
    color: var(--brand-red);
    text-transform: uppercase;
    letter-spacing: 0.3px;
  }
  .contact__line {
    font-size: 17px;
    color: var(--ink);
    line-height: 22px;
  }
  .contact__phone { margin-top: 6px; }
  .tagline {
    margin-top: 12px;
    font-weight: 700;
    font-size: 17px;
    color: var(--ink-strong);
    line-height: 22px;
  }
  .payments {
    font-size: 17px;
    color: var(--ink);
    line-height: 24px;
  }
</style>
</head>
<body>
  <section class="card card--front">
    <div class="brand">
      <span class="brand__dot"></span>
      <span class="brand__name">Ridgeline Plumbing</span>
    </div>
  </section>

  <section class="card card--back">
    <div class="brand">
      <span class="brand__dot"></span>
      <span class="brand__name">Ridgeline Plumbing</span>
    </div>
    <p class="contact__name">Daniel Marsh</p>
    <p class="contact__line contact__phone">0487 312 654</p>
    <p class="contact__line">info@ridgelineplumbing.com.au</p>
    <p class="tagline">“Your local plumbing experts"</p>
    <p class="payments">Emblems for zelpa card, cheque and cash</p>
  </section>
</body>
</html>
```